New Webpage for High Class Expert Witness Services Company

We are looking for a minimalist design for a webpage that just has our logo and an entry form offer to connect with one of our Liaisons.
The entry form should just ask for Name, Email, Contact Info and Description of Project.

Company Name is: The Marlowe Crest Advisory Services

Number of Pages Required

1 page

```html
<!DOCTYPE html>
<html lang="en">
<head>
<meta charset="utf-8">
<title>Marlowe Crest Advisory Services — Connect With a Liaison</title>
<link rel="stylesheet" href="https://fonts.googleapis.com/css2?family=Cinzel:wght@400;600&family=Roboto:wght@400&display=swap">
<style>
  :root {
    --bg-deep: #0d0d0d;
    --bg-mid: #1b1b1b;
    --panel-edge: #5a5a5a;
    --field-edge: #d8d8d8;
    --text-light: #f2f2f2;
    --text-silver: #c9c9c9;
    --text-muted: #8d8d8d;
    --gold-dark: #b8902a;
    --gold-light: #f0cf68;
    --rule: #3a3a3a;
  }
  * { box-sizing: border-box; margin: 0; padding: 0; }
  html, body { width: 1200px; height: 744px; overflow: hidden; }
  body {
    position: relative;
    background:
      radial-gradient(ellipse 420px 360px at 470px 290px, rgba(70,70,70,0.45), transparent 70%),
      linear-gradient(180deg, var(--bg-mid), var(--bg-deep));
    color: var(--text-light);
    font-family: "Roboto", Arial, sans-serif;
  }
  .brand {
    position: absolute; left: 132px; top: 62px;
    display: flex; align-items: center; gap: 12px;
  }
  .brand-mark { width: 14px; height: 14px; background: var(--text-silver); }
  .brand-name {
    font-family: "Cinzel", Georgia, serif; font-weight: 400;
    font-size: 25px; letter-spacing: 1px; color: var(--text-silver);
  }
  .hero { position: absolute; left: 136px; top: 270px; }
  .hero-eyebrow {
    font-family: "Cinzel", Georgia, serif; font-size: 18px;
    letter-spacing: 2.2px; color: var(--text-muted);
  }
  .hero-title {
    margin-top: 12px;
    font-family: "Cinzel", Georgia, serif; font-weight: 400;
    font-size: 43px; line-height: 58px; letter-spacing: 1.5px;
    color: var(--text-silver);
  }
  .liaison-panel {
    position: absolute; left: 716px; top: 96px; width: 379px; height: 512px;
    border: 1px solid var(--panel-edge);
    background: radial-gradient(ellipse at 60% 40%, rgba(60,60,60,0.5), rgba(15,15,15,0.9));
    padding: 34px 0 0 45px;
  }
  .liaison-title {
    font-family: "Cinzel", Georgia, serif; font-weight: 400;
    font-size: 21px; letter-spacing: 0.5px; margin-left: 1px;
  }
  .field {
    display: block; width: 296px; height: 42px; margin-top: 16px;
    border: 1px solid var(--field-edge); background: transparent;
    color: var(--text-light); font: 13px "Roboto", Arial, sans-serif;
    padding: 0 18px;
  }
  .field::placeholder { color: var(--text-light); }
  .liaison-title + .field { margin-top: 22px; }
  .field-area { height: 88px; padding-top: 12px; resize: none; }
  .submit-btn {
    display: block; width: 299px; height: 44px; margin-top: 13px;
    border: 0; cursor: pointer;
    background: linear-gradient(90deg, var(--gold-dark), var(--gold-light) 35%, #c9a23e 60%, var(--gold-light) 85%, var(--gold-dark));
    font-family: "Cinzel", Georgia, serif; font-weight: 600; font-size: 15px;
    letter-spacing: 0.5px; color: #141414;
  }
  .divider {
    display: flex; align-items: center; gap: 14px; width: 270px;
    margin: 12px 0 0 15px; font-size: 13px; color: var(--text-light);
  }
  .divider::before, .divider::after { content: ""; flex: 1; height: 1px; background: var(--rule); }
  .liaison-phone {
    margin-top: 10px; width: 299px; text-align: center;
    font-family: "Cinzel", Georgia, serif; font-size: 32px; color: var(--text-light);
  }
  .site-footer {
    position: absolute; left: 0; top: 682px; width: 1200px; height: 62px;
    border-top: 1px solid var(--rule);
    display: flex; align-items: center; justify-content: center;
    font-size: 12px; color: var(--text-muted);
  }
</style>
</head>
<body>
  <header class="brand">
    <span class="brand-mark"></span>
    <span class="brand-name">MARLOWE CREST ADVISORY SERVICES</span>
  </header>

  <section class="hero">
    <p class="hero-eyebrow">MARLOWE CREST ADVISORY SERVICES</p>
    <h1 class="hero-title">SEAMLESS MEDICAL<br>EXPERT INTEGRATION</h1>
  </section>

  <form class="liaison-panel">
    <h2 class="liaison-title">CONNECT WITH A LIAISON</h2>
    <input class="field" type="text" placeholder="Name*">
    <input class="field" type="email" placeholder="Email*">
    <input class="field" type="tel" placeholder="Phone number*">
    <textarea class="field field-area" placeholder="Description of Project"></textarea>
    <button class="submit-btn" type="button">SUBMIT</button>
    <div class="divider">or</div>
    <p class="liaison-phone">800-555-0142</p>
  </form>

  <footer class="site-footer">© 2026 Marlowe Crest Advisory Services. All Rights Reserved</footer>
</body>
</html>
```